Stationery Design Project

I need a stationary design for our company. we are based in Houston, TX and we are called Mira Vell Lending. And we are wanting to brand our MoneyMendPlus program, which includes our tax preparation and restoration, credit repair service. Although our business offers other programs, we are interested in mainly focusing on The MoneyMendPlus program. We are looking for way to brand our ourselves and I believe that a great stationery design will help in achieving this goal. Our logo design is blue and light blue. the slogan is orange.

Industry/Entity Type

Business

Requirements
Must have
• Address: 30871 Calloway Ln. B-22
Houston, TX 75419
Tel. 555-318-6207
Fax 555-294-7153
www.miravelllending.example
info@miravelllending.example
Our Slogan: Confidence, Renewed!

```html
<!DOCTYPE html>
<html lang="en">
<head>
<meta charset="utf-8">
<title>Mira Vell Lending – Business Card</title>
<link rel="stylesheet" href="https://fonts.googleapis.com/css2?family=Tinos:wght@400;700&display=swap">
<style>
  :root {
    --navy: #163f66;
    --navy-light: #b9cde3;
    --sky: #1f8fcf;
    --orange: #f39a1e;
    --ink: #2a2a2a;
    --paper: #ffffff;
    --stage: #e9e9ea;
    --rule: #9aa7b5;
  }
  * { margin: 0; padding: 0; box-sizing: border-box; }
  html, body {
    width: 1200px; height: 724px; overflow: hidden;
    background: var(--stage);
    font-family: "Tinos", "Times New Roman", serif;
    color: var(--ink);
  }
  .card {
    position: absolute;
    width: 540px; height: 310px;
    background: var(--paper);
    border-radius: 22px;
    box-shadow: 0 4px 14px rgba(0,0,0,.18);
    overflow: hidden;
  }
  .card--front { left: 40px; top: 207px; }
  .card--back  { left: 620px; top: 207px; }

  /* front */
  .brand-block {
    position: absolute; left: 72px; top: 62px;
    width: 130px; height: 140px;
    background: var(--navy);
    border: 5px solid var(--navy-light);
    display: flex; align-items: flex-end; justify-content: center;
    padding-bottom: 18px;
  }
  .brand-block__name {
    color: var(--paper); font-size: 13px; text-align: center; line-height: 1.2;
  }
  .divider {
    position: absolute; left: 232px; top: 30px;
    width: 2px; height: 160px;
    background: linear-gradient(to bottom, transparent, var(--rule), transparent);
  }
  .contact {
    position: absolute; left: 252px; top: 34px;
    font-size: 15px; line-height: 1.25; list-style: none;
  }
  .contact__address { margin-bottom: 14px; }
  .contact__item { display: flex; align-items: center; gap: 8px; line-height: 1.35; }
  .contact__item svg { width: 12px; height: 12px; fill: var(--navy); flex: none; }
  .slogan-band {
    position: absolute; left: 0; right: 0; top: 220px; height: 30px;
    background: var(--navy);
    display: flex; align-items: center; padding-left: 96px;
  }
  .slogan-band::before, .slogan-band::after {
    content: ""; position: absolute; left: 0; right: 0; height: 1px; background: var(--navy);
  }
  .slogan-band::before { top: -6px; }
  .slogan-band::after { bottom: -6px; }
  .slogan {
    color: var(--orange); font-weight: 700; font-size: 17px; letter-spacing: 6px;
  }

  /* back */
  .program {
    position: absolute; left: 0; right: 0; top: 118px;
    display: flex; align-items: center; justify-content: center; gap: 12px;
  }
  .program__mark { width: 26px; height: 26px; background: var(--sky); }
  .program__name { color: var(--sky); font-size: 50px; line-height: 1; }
  .program__rule {
    position: absolute; left: 70px; right: 90px; top: 178px; height: 3px; background: var(--navy);
  }
  .site {
    position: absolute; left: 0; right: 0; top: 236px; text-align: center;
    font-size: 13px; letter-spacing: 5px; color: var(--ink);
  }
  .site b { color: var(--navy); }
</style>
</head>
<body>
  <section class="card card--front" aria-label="Business card front">
    <div class="brand-block"><span class="brand-block__name">Mira Vell Lending</span></div>
    <div class="divider"></div>
    <ul class="contact">
      <li class="contact__address">30871 Calloway Ln. B-22<br>Houston, TX 75419</li>
      <li class="contact__item">
        <svg viewBox="0 0 12 12" aria-hidden="true"><path d="M2 1h3l1 3-2 1a7 7 0 0 0 3 3l1-2 3 1v3c-6 0-9-3-9-9z"/></svg>555-318-6207
      </li>
      <li class="contact__item">
        <svg viewBox="0 0 12 12" aria-hidden="true"><rect x="3" y="1" width="6" height="3"/><rect x="1" y="5" width="10" height="5" rx="1"/></svg>555-294-7153
      </li>
      <li class="contact__item">
        <svg viewBox="0 0 12 12" aria-hidden="true"><path d="M1 3h10v7H1z M1 3l5 4 5-4" stroke="#fff" stroke-width=".8"/></svg>info@miravelllending.example
      </li>
      <li class="contact__item">
        <svg viewBox="0 0 12 12" aria-hidden="true"><circle cx="6" cy="6" r="5"/><path d="M1 6h10M6 1v10" stroke="#fff" stroke-width=".8"/></svg>www.miravelllending.example
      </li>
    </ul>
    <div class="slogan-band"><span class="slogan">Confidence, Renewed!</span></div>
  </section>

  <section class="card card--back" aria-label="Business card back">
    <div class="program">
      <span class="program__mark"></span>
      <span class="program__name">MoneyMendPlus</span>
    </div>
    <div class="program__rule"></div>
    <p class="site">www.<b>miravelllending</b>.example</p>
  </section>
</body>
</html>
```